Cover for Lanterns Along the Quiet Shore of Being

Cover for a book that describes everything that happens to a person, from pre-birth life plans through growing in compassion and wisdom to death and living in the afterlife. The information is revealed in messages from people living in the life after this life. The title is Lessons Gathered From Every Season of Your Existence: Shared by Voices Dwelling Beyond the Veil. Author is T. Wesley Prandt. Book size is 6 by 9.

Target Market(s)

General

Font styles to use
Serif

```html
<!DOCTYPE html>
<html lang="en">
<head>
<meta charset="utf-8">
<title>Lessons Gathered From Every Season of Your Existence — Cover</title>
<link rel="stylesheet" href="https://fonts.googleapis.com/css2?family=Cinzel:wght@400;600;700&family=Cormorant+Garamond:wght@600;700&family=Cormorant+SC:wght@500;600&display=swap">
<style>
  :root {
    --page-bg: #ffffff;
    --ink-dark: #1c1710;
    --title-amber: #c7813a;
    --author-cream: #f1e9da;
    --spine-bg: #ecebea;
    --spine-ink: #2a2520;
    --sky-warm: #cdb593;
    --sky-glow: #f7f1e3;
    --field-deep: #1d2218;
    --bloom-amber: #e0a526;
  }
  html, body {
    margin: 0;
    padding: 0;
    width: 1200px;
    height: 1200px;
    overflow: hidden;
    background: var(--page-bg);
  }
  .canvas {
    position: relative;
    width: 1200px;
    height: 1200px;
  }

  /* Front cover */
  .front-cover {
    position: absolute;
    left: 232px;
    top: 194px;
    width: 572px;
    height: 880px;
    overflow: hidden;
  }
  .cover-art {
    position: absolute;
    inset: 0;
    background:
      radial-gradient(ellipse 34% 20% at 50% 74%, rgba(224,165,38,0.95) 0%, rgba(150,80,20,0.85) 45%, rgba(224,165,38,0) 100%),
      radial-gradient(ellipse 70% 32% at 50% 38%, var(--sky-glow) 0%, rgba(247,241,227,0.7) 45%, rgba(247,241,227,0) 100%),
      linear-gradient(180deg, #9c8266 0%, var(--sky-warm) 16%, #e9dcc4 38%, #d9cdb4 54%, #6d6a45 64%, #3a3d26 76%, var(--field-deep) 100%);
  }
  .cover-text {
    position: absolute;
    left: 0;
    width: 100%;
    margin: 0;
    text-align: center;
    white-space: nowrap;
  }
  .kicker {
    font-family: "Cinzel", serif;
    font-weight: 600;
    font-size: 22px;
    letter-spacing: 2.5px;
    color: var(--ink-dark);
  }
  .kicker-line-1 { top: 62px; }
  .kicker-line-2 { top: 114px; }
  .headline {
    font-family: "Cinzel", serif;
    font-weight: 700;
    font-size: 56px;
    letter-spacing: 3px;
    color: var(--title-amber);
    line-height: 1;
  }
  .headline-line-1 { top: 168px; }
  .headline-line-2 { top: 246px; }
  .subtitle {
    top: 398px;
    font-family: "Cormorant SC", serif;
    font-weight: 600;
    font-size: 17px;
    letter-spacing: 1.4px;
    color: var(--ink-dark);
  }
  .author {
    top: 786px;
    font-family: "Cormorant Garamond", serif;
    font-weight: 700;
    font-size: 29px;
    letter-spacing: 1.5px;
    color: var(--author-cream);
  }

  /* Spine */
  .spine {
    position: absolute;
    left: 838px;
    top: 194px;
    width: 106px;
    height: 880px;
    background: var(--spine-bg);
  }
  .spine-text {
    position: absolute;
    writing-mode: vertical-rl;
    margin: 0;
    white-space: nowrap;
  }
  .spine-author {
    left: 44px;
    top: 94px;
    font-family: "Cormorant Garamond", serif;
    font-weight: 600;
    font-size: 21px;
    letter-spacing: 1px;
    color: var(--spine-ink);
  }
  .spine-kicker {
    left: 70px;
    top: 428px;
    font-family: "Cinzel", serif;
    font-weight: 600;
    font-size: 12.5px;
    letter-spacing: 0.6px;
    color: var(--spine-ink);
  }
  .spine-headline {
    left: 40px;
    top: 428px;
    font-family: "Cinzel", serif;
    font-weight: 700;
    font-size: 27px;
    letter-spacing: 2px;
    color: var(--title-amber);
  }
  .spine-subtitle {
    left: 18px;
    top: 428px;
    font-family: "Cormorant SC", serif;
    font-weight: 600;
    font-size: 12px;
    letter-spacing: 0.4px;
    color: var(--spine-ink);
  }
</style>
</head>
<body>
<main class="canvas">
  <section class="front-cover">
    <div class="cover-art" role="img" aria-label="Photograph of a sunflower field at sunset, a hand holding up a single sunflower beneath a glowing sky with a faint figure in the clouds"></div>
    <p class="cover-text kicker kicker-line-1">LESSONS GATHERED FROM</p>
    <p class="cover-text kicker kicker-line-2">EVERY SEASON OF</p>
    <h1 class="cover-text headline headline-line-1">YOUR</h1>
    <h1 class="cover-text headline headline-line-2">EXISTENCE</h1>
    <p class="cover-text subtitle">Shared by Voices Dwelling Beyond the Veil</p>
    <p class="cover-text author">T. Wesley Prandt</p>
  </section>

  <aside class="spine">
    <p class="spine-text spine-author">T. Wesley Prandt</p>
    <p class="spine-text spine-kicker">LESSONS GATHERED FROM EVERY SEASON OF</p>
    <p class="spine-text spine-headline">YOUR EXISTENCE</p>
    <p class="spine-text spine-subtitle">Shared by Voices Dwelling Beyond the Veil</p>
  </aside>
</main>
</body>
</html>
```